indépendant en tant que Massothérapeute et Préparateur Mental, j'ai besoin de ...

Massothérapeute et préparateur mental indépendant, je recherche une carte de visite sobre et dynamique, sans images liées au massage ou à la préparation mentale mais intégrant mon logo. Les couleurs que j'aime bien sont : Blanc, gris, anthracite, noir et jaune

Contact Information for Business Card

carte de préférence Horizontale
neutre qui puisse toucher le deux domaines Massothérapie et préparation mentale

Requirements
Must have
• mon projet doit intégrer au recto:
LOGO
Loïc Bardèze
078 513 26 48
info@loicbardeze.ch
et éventuellement www.loicbardeze.ch

et au verso les deux adresses:

Chemin des Ormilles 7B
1400 Yverdon-les-Bains

Route de la Gravière 9
1700 Fribourg

Should not have
• mon projet ne doit pas contenir d'image en liens avec le massage ni la préparation mentale.

```html
<!DOCTYPE html>
<html lang="fr">
<head>
<meta charset="utf-8">
<title>Loïc Bardèze – cartes de visite</title>
<link rel="stylesheet" href="https://fonts.googleapis.com/css2?family=Lato:wght@400;700&display=swap">
<style>
  :root {
    --bg: #141414;
    --card: #2d2d2f;
    --white: #f4f4f4;
    --yellow: #f2b705;
    --yellow-line: #c9a21a;
    --grey: #bdbdbd;
  }
  * { margin: 0; padding: 0; box-sizing: border-box; }
  html, body { width: 1200px; height: 896px; overflow: hidden; background: var(--bg); }
  body { position: relative; font-family: "Lato", Arial, sans-serif; color: var(--white); }

  .card {
    position: absolute;
    width: 540px;
    height: 310px;
    background: var(--card);
    border-bottom: 6px solid var(--yellow);
    box-shadow: 0 14px 30px rgba(0,0,0,.6);
    overflow: hidden;
  }
  .card--addresses { left: 40px; top: 110px; }
  .card--contact { left: 620px; top: 476px; }

  .brand { position: absolute; display: flex; align-items: center; gap: 12px; }
  .brand__dot { width: 14px; height: 14px; border-radius: 50%; background: var(--white); flex: none; }
  .brand__name { font-weight: 700; font-size: 30px; letter-spacing: .5px; line-height: 1; }
  .brand__role { font-size: 8.5px; letter-spacing: 1.1px; text-transform: uppercase; margin-top: 5px; }

  .card--addresses .brand { left: 90px; top: 62px; }
  .card--contact .brand { left: 150px; top: 58px; }

  .addresses { position: absolute; left: 130px; top: 175px; list-style: none; font-size: 17px; }
  .addresses li { display: flex; align-items: center; gap: 10px; margin-bottom: 12px; }
  .addresses li:nth-child(2) { margin-left: 50px; }

  .icon { width: 12px; height: 12px; flex: none; }

  .holder { position: absolute; left: 34px; top: 178px; }
  .holder__name { font-weight: 700; font-size: 19px; text-transform: uppercase; }
  .holder__title { font-size: 15px; margin-top: 2px; }

  .divider { position: absolute; left: 34px; right: 34px; top: 228px; height: 1px; background: var(--yellow-line); }

  .contacts { position: absolute; left: 48px; top: 240px; list-style: none; font-size: 15px; }
  .contacts li { display: flex; align-items: center; gap: 8px; margin-bottom: 3px; }

  .website { position: absolute; right: 34px; top: 246px; font-size: 14px; }
  .website span { color: var(--yellow); }
</style>
</head>
<body>
  <section class="card card--addresses">
    <div class="brand">
      <span class="brand__dot"></span>
      <div>
        <div class="brand__name">Loïc Bardèze</div>
        <div class="brand__role">Massothérapeute / Préparateur mental</div>
      </div>
    </div>
    <ul class="addresses">
      <li><svg class="icon" viewBox="0 0 12 12"><path d="M6 0.5a4 4 0 0 0-4 4c0 3 4 7 4 7s4-4 4-7a4 4 0 0 0-4-4z" fill="#f2b705"/><circle cx="6" cy="4.5" r="1.5" fill="#2d2d2f"/></svg>Chemin des Ormilles 7B, 1400 Yverdon-les-Bains</li>
      <li><svg class="icon" viewBox="0 0 12 12"><path d="M6 0.5a4 4 0 0 0-4 4c0 3 4 7 4 7s4-4 4-7a4 4 0 0 0-4-4z" fill="#f2b705"/><circle cx="6" cy="4.5" r="1.5" fill="#2d2d2f"/></svg>Route de la Gravière 9, 1700 Freiburg</li>
    </ul>
  </section>

  <section class="card card--contact">
    <div class="brand">
      <span class="brand__dot"></span>
      <div>
        <div class="brand__name">Loïc Bardèze</div>
        <div class="brand__role">Massothérapeute / Préparateur mental</div>
      </div>
    </div>
    <div class="holder">
      <div class="holder__name">Loïc Bardèze</div>
      <div class="holder__title">Founder &amp; CEO</div>
    </div>
    <div class="divider"></div>
    <ul class="contacts">
      <li><svg class="icon" viewBox="0 0 12 12"><path d="M2.5 1l2 2.2-1 1.3a7 7 0 0 0 4 4l1.3-1 2.2 2-1.3 1.5C5 10.5 1.5 7 1 2.3z" fill="#f2b705"/></svg>078 513 26 48</li>
      <li><svg class="icon" viewBox="0 0 12 12"><rect x="0.5" y="2.5" width="11" height="7" fill="#f2b705"/><path d="M0.5 2.5l5.5 4 5.5-4" stroke="#2d2d2f" fill="none"/></svg>info@loicbardeze.ch</li>
    </ul>
    <div class="website">www.<span>loicbardeze</span>.ch</div>
  </section>
</body>
</html>
```